Automotive Accessories Business Card

Design a business template that match our new logo design and our industry.

https://www.qelmotorgear.com/

Target Market(s)

Aftermarket auto parts and accessories

Industry/Entity Type

automotive

Contact Information for Business Card

company logo

Font styles to use
Serif
Sans Serif

Colors
EB3D1F
EC4F4E
F09395
F8D3D4
FCEDEE

```html
<!DOCTYPE html>
<html lang="en">
<head>
<meta charset="utf-8">
<title>QEL Motor Gear – Business Card</title>
<link rel="stylesheet" href="https://fonts.googleapis.com/css2?family=Audiowide&family=Roboto:wght@400;500;700&display=swap">
<style>
:root{
  --stage:#8e8e8e;
  --paper:#ffffff;
  --red:#d81f26;
  --ink:#3a3a3a;
  --charcoal:#414042;
  --black:#050505;
}
*{margin:0;padding:0;box-sizing:border-box}
html,body{width:1200px;height:1200px;overflow:hidden;background:var(--stage)}
.card{position:absolute;left:281px;width:639px;height:366px;overflow:hidden;box-shadow:2px 3px 6px rgba(0,0,0,.35)}
.card-front{top:195px;background:var(--paper)}
.card-back{top:639px;background:radial-gradient(ellipse at 50% 30%,#3a3a3a 0%,#1a1a1a 45%,var(--black) 85%)}
.identity{position:absolute;right:358px;top:140px;text-align:right}
.identity .name{font-family:"Audiowide",sans-serif;color:var(--red);font-size:29px;line-height:1;letter-spacing:-.5px;text-transform:uppercase}
.identity .role{font-family:"Roboto",sans-serif;color:var(--ink);font-size:19px;margin-top:4px}
.divider{position:absolute;left:311px;top:110px;width:2px;height:120px;background:var(--red)}
.contact{position:absolute;left:349px;top:110px;font-family:"Roboto",sans-serif;color:var(--ink);font-size:17.5px;letter-spacing:.4px;list-style:none}
.contact li{display:flex;align-items:flex-start;line-height:22.5px}
.contact li+li{margin-top:9px}
.contact svg{width:14px;height:14px;margin:4px 13px 0 0;flex:none;fill:var(--red)}
.checker-strip{position:absolute;left:0;top:293px;width:152px;height:13px;background:linear-gradient(90deg,var(--charcoal),var(--red))}
.web-band{position:absolute;left:0;top:306px;width:639px;height:31px}
.web-band svg{position:absolute;inset:0}
.web-band .url{position:absolute;left:0;width:600px;top:0;height:31px;line-height:31px;text-align:center;font-family:"Roboto",sans-serif;color:#fff;font-size:14.5px;letter-spacing:3px}
.web-band .url b{font-weight:700}
.band-name{position:absolute;left:530px;top:0;height:31px;line-height:31px;font-family:"Audiowide",sans-serif;font-size:17px;color:#fff}
.back-brand{position:absolute;left:0;right:0;top:155px;display:flex;justify-content:center;align-items:center;gap:16px}
.back-brand .mark{width:34px;height:34px;background:var(--red)}
.back-brand .wordmark{font-family:"Audiowide",sans-serif;color:#fff;font-size:44px;letter-spacing:1px}
</style>
</head>
<body>
<section class="card card-front">
  <div class="identity">
    <p class="name">Dana Reyes</p>
    <p class="role">Founder &amp; CEO</p>
  </div>
  <div class="divider"></div>
  <ul class="contact">
    <li><svg viewBox="0 0 14 14"><path d="M7 0a5 5 0 0 0-5 5c0 3.6 5 9 5 9s5-5.4 5-9a5 5 0 0 0-5-5zm0 7a2 2 0 1 1 0-4 2 2 0 0 1 0 4z"/></svg><span>240 W. Harbor Ave. Unit B<br>Riverton, CA, 92504<br>United States</span></li>
    <li><svg viewBox="0 0 14 14"><path d="M3 0l2.5 3.5-1.5 2c.8 1.8 2.2 3.3 4 4l2-1.5L14 10.5 12 14C5.5 13.5.5 8.5 0 2z"/></svg><span>1-800-555-0142</span></li>
    <li style="margin-top:4px"><svg viewBox="0 0 14 14"><path d="M0 3h14v9H0zM1 4l6 4 6-4"/></svg><span>sales@qelmotorgear.com</span></li>
  </ul>
  <div class="checker-strip" role="img" aria-label="Racing checker strip"></div>
  <div class="web-band">
    <svg width="639" height="31" viewBox="0 0 639 31">
      <polygon points="0,0 495,0 470,31 0,31" fill="#d81f26"/>
      <polygon points="500,0 639,0 639,31 475,31" fill="#414042"/>
    </svg>
    <p class="url">www.<b>QELMOTORGEAR</b>.com</p>
    <span class="band-name">QEL</span>
  </div>
</section>
<section class="card card-back" role="img" aria-label="Dark perforated metal texture">
  <div class="back-brand">
    <span class="mark"></span>
    <span class="wordmark">QEL MOTOR GEAR</span>
  </div>
</section>
</body>
</html>
```